Lantern Petals Website v.1 - attract floral shop franchisees

I need a simple information website for my new business. We are a franchisor of flower shops. The overall purpose of the website is to promote the company and the service, especially to potential franchisees and retailers. Only about 4 pages are required including homepage, About, For Supermarkets, For Franchisees, and Contact. No special functions are required except the site will have two separate inquiry forms that must be filled out online and submitted via automated email. Similarly, an email form should be linked from the Contact page. I have a logo and business cards designed by ArtMingle, and I would like the site to have a consistent color scheme and style. The key to design will be to express the joy and love associated with flowers and floral bouquets.
IMPORTANT - I will be exporting the website design to Wordpress CMS in a site hosted by HostNimbus. For smooth integration into WordPress hosted by HostNimbus, the designer should build the site using a WordPress-friendly format. Ideally, they should use HTML, CSS, and PHP. Creating a custom theme or using a page builder that exports to WordPress-compatible files is best. This ensures the site can be easily imported and managed within WordPress.

Target Market(s)

Potential franchisees (existing florists or creative types who might like to own a floral business) and supermarkets who might want us to run their floral department

Industry/Entity Type

Floral retailing

Requirements
Must have
• A brand theme that is beautiful, consistent throughout and builds on the logo design
Nice to have
• Show gender and ethnic diversity in customers and florists. Pictures of happy florists (for franchisees) and pictures of amazing floral department displays (for supermarkets)

```html
<!DOCTYPE html>
<html lang="en">
<head>
<meta charset="utf-8">
<title>Lantern Petals – Flower Shop Franchising</title>
<link rel="stylesheet" href="https://fonts.googleapis.com/css2?family=Poppins:wght@400;500;600;700;800&family=Great+Vibes&display=swap">
<style>
:root{
  --orange:#f39a12;
  --orange-dark:#e58a00;
  --ink:#1d1d1d;
  --text:#3a3a3a;
  --muted:#666;
  --green:#1f9d43;
  --green-bar:#22c24a;
  --mint:#dcefdc;
  --cream:#f6f1df;
  --black:#111;
  --white:#fff;
  --line:#e3e3e3;
  --red-arrow:#ef3b1c;
}
*{box-sizing:border-box;margin:0;padding:0}
html,body{width:1200px;height:4521px;overflow:hidden}
body{position:relative;background:var(--white);font-family:'Poppins',sans-serif;color:var(--text)}
.abs{position:absolute}
.script{font-family:'Great Vibes',cursive;font-weight:400;color:var(--ink)}
.btn{position:absolute;display:flex;align-items:center;height:34px;padding:0 4px 0 16px;border-radius:17px;background:var(--orange);color:var(--white);font-size:11px;font-weight:500;gap:12px}
.btn .dot{width:28px;height:28px;border-radius:50%;background:var(--white);display:flex;align-items:center;justify-content:center}
.btn .dot i{width:14px;height:14px;border-radius:50%;border:3px solid var(--orange)}
.photo{position:absolute}
.brand{display:flex;align-items:center;gap:12px;font-weight:600;color:var(--orange)}
.brand .mark{width:40px;height:40px;border-radius:50%;border:3px solid var(--orange)}
.sec-title{position:absolute;font-weight:700;font-size:34px;color:var(--ink);white-space:nowrap;display:flex;align-items:baseline;gap:8px}
.sec-title .script{font-size:64px;line-height:1}
.sprig{display:inline-block;width:14px;height:40px;border-left:3px dotted var(--green);border-radius:0 0 0 20px;margin-right:4px}

/* header */
.nav{position:absolute;top:57px;left:614px;display:flex;gap:38px;font-size:12px;color:var(--ink)}
.nav .active{color:var(--orange);border-bottom:2px solid var(--orange);padding-bottom:3px}
.hero-title{position:absolute;left:140px;top:204px;font-size:36px;font-weight:700;line-height:42px;color:var(--ink)}
.hero-text{position:absolute;left:142px;top:342px;width:460px;font-size:11px;line-height:19px;color:var(--ink)}

/* about */
.about-band{position:absolute;left:0;top:640px;width:1200px;height:605px;background:linear-gradient(90deg,#f5f2e8 0%,#e8f2e2 60%,#d9ecd7 100%)}
.about-frame{position:absolute;left:175px;top:754px;width:351px;height:396px;background:var(--white);border-radius:26px;padding:10px;box-shadow:0 8px 24px rgba(0,0,0,.08)}
.about-frame .photo{position:static;width:100%;height:100%;border-radius:20px}
.badge{position:absolute;left:392px;top:1055px;width:130px;height:130px;border-radius:50%;background:#fff;border:10px solid #f4f4f4;box-shadow:0 4px 12px rgba(0,0,0,.1)}
.about-copy{position:absolute;left:600px;top:828px;width:460px;font-size:11px;line-height:20px;color:var(--ink)}
.about-copy p+p{margin-top:20px}

/* opportunity */
.card{position:absolute;top:1466px;width:280px;height:356px;background:var(--white);border-radius:18px;padding:10px;box-shadow:0 6px 18px rgba(0,0,0,.08)}
.card .photo{position:relative;width:100%;height:100%;border-radius:14px;display:flex;flex-direction:column;align-items:center;justify-content:flex-end;padding-bottom:30px}
.card h3{color:var(--white);font-size:20px;font-weight:600;text-align:center;line-height:26px;text-shadow:0 2px 6px rgba(0,0,0,.4)}
.card .go{margin-top:14px;width:26px;height:26px;border-radius:50%;background:var(--orange);display:flex;align-items:center;justify-content:center}

/* why */
.why-band{position:absolute;left:0;top:2014px;width:1200px;height:608px;background:linear-gradient(90deg,#d8ebd7 0%,#e6f1e1 45%,#eef2e8 100%)}
.why-list{position:absolute;left:142px;top:2200px;list-style:none;font-size:11px;color:var(--ink)}
.why-list li{height:28.4px;display:flex;align-items:center;gap:12px}

/* growth */
.growth-text{position:absolute;left:275px;top:2795px;width:650px;text-align:center;font-size:11px;line-height:20px;color:var(--ink)}

/* faq */
.faq-band{position:absolute;left:0;top:3192px;width:1200px;height:650px;background:linear-gradient(90deg,#f7ecd3 0%,#eef0dc 50%,#d6ebd6 100%)}
.faq{position:absolute;left:286px;width:628px;background:var(--white);border:1px solid var(--line);font-size:12px;color:var(--ink);letter-spacing:.4px}
.faq .q{height:49px;display:flex;align-items:center;justify-content:space-between;padding:0 22px}
.faq .q b{font-size:20px;font-weight:500}
.faq.open{border-bottom:6px solid var(--green)}
.faq.open .q{font-weight:600;letter-spacing:0}
.faq .a{margin:0 22px;padding:12px 0 14px;border-top:1px solid var(--line);font-size:11px;line-height:22px;text-align:justify;color:var(--muted)}

/* contact */
.contact-ghost{position:absolute;left:70px;top:3850px;font-size:190px;font-weight:800;letter-spacing:30px;color:rgba(0,0,0,.05)}
.footer{position:absolute;left:0;top:4201px;width:1200px;height:320px;background:var(--black)}
.contact-card{position:absolute;left:175px;top:3996px;width:848px;height:347px;display:flex;box-shadow:0 10px 30px rgba(0,0,0,.12)}
.contact-form{width:495px;background:var(--white);position:relative}
.contact-form h2,.contact-info h2{font-size:26px;font-weight:600;color:var(--ink)}
.field{position:absolute;height:34px;border:1px solid #ccc;font-size:10px;color:#777;padding:10px}
.contact-info{flex:1;background:linear-gradient(180deg,#e9f3e4,#d9ecd6);position:relative;padding:48px 34px}
.info-row{display:flex;align-items:center;gap:14px;font-size:11px;color:var(--ink);margin-bottom:24px}
.ico{width:28px;height:28px;border-radius:50%;border:1.5px solid var(--orange);display:flex;align-items:center;justify-content:center;flex:none}
.social{display:flex;gap:16px;font-size:11px;color:var(--ink)}
.social span{display:flex;align-items:center;gap:8px}
.social i{width:26px;height:26px;border-radius:50%;border:1.5px solid var(--orange)}
.foot-nav{position:absolute;left:502px;top:4395px;display:flex;gap:38px;font-size:12px;color:var(--white)}
.copyright{position:absolute;left:0;top:4485px;width:1200px;text-align:center;font-size:11px;color:var(--white)}
</style>
</head>
<body>

<!-- header & hero -->
<div class="photo" role="img" aria-label="Soft watercolour floral background" style="left:0;top:0;width:1200px;height:640px;background:radial-gradient(circle at 80% 20%,#e8f1ef 0,#fff 45%),radial-gradient(circle at 10% 30%,#f7efe3 0,transparent 40%)"></div>
<div class="photo" role="img" aria-label="Pink gerbera flowers" style="left:10px;top:95px;width:130px;height:150px;border-radius:50%;background:radial-gradient(circle,#e8367c 0,#f59ac0 60%,transparent 72%)"></div>
<div class="photo" role="img" aria-label="Peach dahlias" style="left:1030px;top:490px;width:170px;height:300px;border-radius:50%;background:radial-gradient(circle,#f07b59 0,#fbc2a8 55%,transparent 72%)"></div>

<div class="abs brand" style="left:150px;top:48px;font-size:28px"><span class="mark"></span>Lantern Petals</div>
<nav class="nav"><span class="active">About Us</span><span>For Supermarkets</span><span>For Franchisees</span><span>Contact Us</span></nav>

<h1 class="hero-title">Flowers Expressed<br>Feelings Of Surprise,<br>Happiness and gratitude.</h1>
<p class="hero-text">Get franchisor of flower shops. Nibh euismod tincidunt ut laoreet dolore magna aliquam erat volutpat. Ut wisi enim ad minim veniam.</p>
<div class="btn" style="left:140px;top:427px">Get Franchisee <span class="dot"><i></i></span></div>

<div class="abs" style="left:645px;top:125px;width:464px;height:464px;border-radius:50%;background:var(--white);box-shadow:0 8px 28px rgba(0,0,0,.12)"></div>
<div class="photo" role="img" aria-label="Shop display of white hydrangeas and pink roses" style="left:657px;top:137px;width:440px;height:440px;border-radius:50%;background:radial-gradient(circle at 45% 40%,#f4f1ec 0,#d64b7f 45%,#3c6b2e 80%)"></div>

<!-- about -->
<div class="about-band"></div>
<div class="photo" role="img" aria-label="Orange roses and red gerberas lying on a table" style="left:0;top:1000px;width:360px;height:320px;border-radius:40%;background:radial-gradient(circle,#f47b2a 0,#f7b26a 45%,transparent 70%)"></div>
<div class="about-frame"><div class="photo" role="img" aria-label="Company founder standing among bouquets in a flower cooler" style="background:linear-gradient(180deg,#9fae8e 0%,#c8c9b8 45%,#e8c23a 80%,#a9c4de 100%)"></div></div>
<div class="badge"></div>

<div class="sec-title" style="left:600px;top:740px"><span class="sprig"></span>About <span class="script">Lantern Petals</span></div>
<div class="about-copy">
  <p>Fresh flowers convey beauty and love, and in our view should become something every person regularly enjoys. Lantern Petals is an entrepreneurial company created to make top quality fresh flowers and professionally-designed bouquets accessible to every consumer at affordable prices.</p>
  <p>Professional florists typically sell the finest quality stems, design the most beautiful bouquets and provide the finest customer service, but their costs – of floral products, retail spaces, labor and marketing – force them to pass high prices along to customers. Supermarket flower departments benefit from high customer footfall, economies of scale and low pricing, but their quality of stems and bouquets is typically poor, staffing is limited, and staff turnover is high which can result in inefficiency, wastage, poorly merchandised selections and limited service.</p>
</div>
<div class="btn" style="left:600px;top:1124px">Get Franchisee <span class="dot"><i></i></span></div>

<!-- opportunity -->
<div class="photo" role="img" aria-label="Faint pastel blossoms background" style="left:0;top:1245px;width:1200px;height:770px;background:radial-gradient(ellipse at 50% 40%,#f8eef0 0,#fff 60%)"></div>
<div class="sec-title" style="left:305px;top:1335px"><span class="sprig"></span>Opportunity For <span class="script">Franchisees</span></div>

<div class="card" style="left:144px"><div class="photo" role="img" aria-label="Florist in a garden centre greenhouse" style="background:linear-gradient(180deg,#b23b3b 0%,#6f8a4d 55%,#3d5a2c 100%)"><h3>Supermarkets</h3><span class="go"><svg width="12" height="12" viewBox="0 0 12 12"><path d="M2 6h8M7 3l3 3-3 3" stroke="#fff" stroke-width="1.6" fill="none"/></svg></span></div></div>
<div class="card" style="left:461px"><div class="photo" role="img" aria-label="Florist arranging pink flowers" style="background:linear-gradient(180deg,#8aa07a 0%,#d89a8c 50%,#6a7d4a 100%)"><h3>New Florist<br>Franchisees</h3><span class="go"><svg width="12" height="12" viewBox="0 0 12 12"><path d="M2 6h8M7 3l3 3-3 3" stroke="#fff" stroke-width="1.6" fill="none"/></svg></span></div></div>
<div class="card" style="left:778px"><div class="photo" role="img" aria-label="Smiling florist holding a basket of flowers" style="background:linear-gradient(180deg,#9fae87 0%,#c97a6a 55%,#5f7a45 100%)"><h3>Professional Floral<br>Retailers</h3><span class="go"><svg width="12" height="12" viewBox="0 0 12 12"><path d="M2 6h8M7 3l3 3-3 3" stroke="#fff" stroke-width="1.6" fill="none"/></svg></span></div></div>
<div class="btn" style="left:512px;top:1859px">Get Franchisee <span class="dot"><i></i></span></div>

<!-- why partner -->
<div class="why-band"></div>
<div class="photo" role="img" aria-label="Florist smelling a bouquet in a flower shop" style="left:675px;top:2070px;width:525px;height:552px;background:linear-gradient(90deg,rgba(230,240,225,0) 0%,#c9b3a6 35%,#a6485a 65%,#8b9a72 100%)"></div>
<div class="photo" role="img" aria-label="Colourful bouquet" style="left:1040px;top:1840px;width:160px;height:220px;border-radius:50%;background:radial-gradient(circle,#e84a5f 0,#f5c23c 40%,#3f7d3a 65%,transparent 72%)"></div>
<div class="sec-title" style="left:142px;top:2115px"><span class="sprig"></span>Why Partner With <span class="script">Lantern Petals</span></div>
<ul class="why-list">
  <li><svg width="14" height="14" viewBox="0 0 14 14"><circle cx="7" cy="7" r="6" fill="none" stroke="#f39a12" stroke-width="1.4"/><path d="M4 7l2 2 4-4" stroke="#f39a12" stroke-width="1.6" fill="none"/></svg>Low investment and high returns.</li>
  <li><svg width="14" height="14" viewBox="0 0 14 14"><circle cx="7" cy="7" r="6" fill="none" stroke="#f39a12" stroke-width="1.4"/><path d="M4 7l2 2 4-4" stroke="#f39a12" stroke-width="1.6" fill="none"/></svg>Ready made business in local locality.</li>
  <li><svg width="14" height="14" viewBox="0 0 14 14"><circle cx="7" cy="7" r="6" fill="none" stroke="#f39a12" stroke-width="1.4"/><path d="M4 7l2 2 4-4" stroke="#f39a12" stroke-width="1.6" fill="none"/></svg>ROI in 12-15 months.</li>
  <li><svg width="14" height="14" viewBox="0 0 14 14"><circle cx="7" cy="7" r="6" fill="none" stroke="#f39a12" stroke-width="1.4"/><path d="M4 7l2 2 4-4" stroke="#f39a12" stroke-width="1.6" fill="none"/></svg>Delivery throughout the City in less then 2 hours.</li>
  <li><svg width="14" height="14" viewBox="0 0 14 14"><circle cx="7" cy="7" r="6" fill="none" stroke="#f39a12" stroke-width="1.4"/><path d="M4 7l2 2 4-4" stroke="#f39a12" stroke-width="1.6" fill="none"/></svg>Help in selecting the right location.</li>
  <li><svg width="14" height="14" viewBox="0 0 14 14"><circle cx="7" cy="7" r="6" fill="none" stroke="#f39a12" stroke-width="1.4"/><path d="M4 7l2 2 4-4" stroke="#f39a12" stroke-width="1.6" fill="none"/></svg>Trained manpower support (Florist).</li>
  <li><svg width="14" height="14" viewBox="0 0 14 14"><circle cx="7" cy="7" r="6" fill="none" stroke="#f39a12" stroke-width="1.4"/><path d="M4 7l2 2 4-4" stroke="#f39a12" stroke-width="1.6" fill="none"/></svg>Training for franchisee and team.</li>
  <li><svg width="14" height="14" viewBox="0 0 14 14"><circle cx="7" cy="7" r="6" fill="none" stroke="#f39a12" stroke-width="1.4"/><path d="M4 7l2 2 4-4" stroke="#f39a12" stroke-width="1.6" fill="none"/></svg>Exclusive merchandise and design support.</li>
  <li><svg width="14" height="14" viewBox="0 0 14 14"><circle cx="7" cy="7" r="6" fill="none" stroke="#f39a12" stroke-width="1.4"/><path d="M4 7l2 2 4-4" stroke="#f39a12" stroke-width="1.6" fill="none"/></svg>Visual merchandising support.</li>
  <li><svg width="14" height="14" viewBox="0 0 14 14"><circle cx="7" cy="7" r="6" fill="none" stroke="#f39a12" stroke-width="1.4"/><path d="M4 7l2 2 4-4" stroke="#f39a12" stroke-width="1.6" fill="none"/></svg>Quality control team for upkeep of store.</li>
</ul>
<div class="btn" style="left:140px;top:2496px">Get Franchisee <span class="dot"><i></i></span></div>

<!-- growth -->
<div class="sec-title" style="left:452px;top:2700px"><span class="sprig"></span>Our <span class="script">Growth</span></div>
<p class="growth-text">Lorem ipsum dolor sit amet, consectetuer adipiscing elit, sed diam nonummy nibh euismod tincidunt ut laoreet dolore magna aliquam erat volutpat. Ut wisi enim ad minim veniam, quis nostrud exerci tation ullamcorper suscipit lobortis nisl ut aliquip ex ea commodo consequat.</p>
<div class="photo" role="img" aria-label="Faint world map backdrop" style="left:280px;top:2870px;width:640px;height:280px;border-radius:30px;background:radial-gradient(ellipse,#eef0f2 0,#fff 70%)"></div>
<svg class="abs" style="left:307px;top:2877px" width="623" height="272" viewBox="0 0 623 272" font-family="Poppins, sans-serif" font-size="7" fill="#333">
  <g fill="#22c24a">
    <rect x="150" y="195" width="22" height="45"/>
    <rect x="205" y="175" width="22" height="65"/>
    <rect x="260" y="148" width="22" height="92"/>
    <rect x="315" y="120" width="22" height="120"/>
    <rect x="370" y="92" width="22" height="148"/>
    <rect x="425" y="58" width="22" height="182"/>
  </g>
  <g>
    <text x="140" y="190">40%</text><text x="196" y="170">60%</text><text x="251" y="143">70%</text>
    <text x="306" y="115">80%</text><text x="361" y="87">90%</text><text x="414" y="53">100%</text>
  </g>
  <path d="M130 170 L420 20" stroke="#ef3b1c" stroke-width="6" fill="none"/>
  <path d="M425 8 L400 18 L418 36 Z" fill="#ef3b1c"/>
  <g font-size="9" fill="#555">
    <text x="155" y="258">2018</text><text x="210" y="258">2019</text><text x="265" y="258">2020</text>
    <text x="320" y="258">2021</text><text x="375" y="258">2022</text><text x="430" y="258">2023</text>
  </g>
</svg>
<div class="photo" role="img" aria-label="Peach dahlias" style="left:0;top:3020px;width:170px;height:260px;border-radius:50%;background:radial-gradient(circle,#f07b59 0,#fbc2a8 55%,transparent 72%)"></div>

<!-- faq -->
<div class="faq-band"></div>
<div class="photo" role="img" aria-label="Mixed purple and pink bouquet" style="left:930px;top:3630px;width:210px;height:300px;border-radius:50%;background:radial-gradient(circle,#a64fb0 0,#e86b8c 40%,#f2c9d9 60%,transparent 72%)"></div>
<div class="sec-title" style="left:298px;top:3270px"><span class="sprig"></span>Frequently Asked <span class="script">Questions</span></div>
<div class="faq open" style="top:3380px"><div class="q">Lorem ipsum dolor sit amet, consectetuer <b>-</b></div><p class="a">Lorem ipsum dolor sit amet, consectetuer adipiscing elit, sed diam nonummy nibh euismod tincidunt ut laoreet dolore magna aliquam erat volutpat. Ut wisi enim ad minim veniam, quis nostrud exerci tation ut aliquip ex ea commodo consequat.</p></div>
<div class="faq" style="top:3534px"><div class="q">Consectetuer Adipiscing Elit, Sed Diam Nonummy Nibh <b>+</b></div></div>
<div class="faq" style="top:3597px"><div class="q">Sed Diam Nonummy &nbsp;Consectetuer Adipiscing Elit <b>+</b></div></div>
<div class="faq" style="top:3661px"><div class="q">Consectetuer Adipiscing Elit, Sed Diam Nonummy Nibh <b>+</b></div></div>
<div class="faq" style="top:3724px"><div class="q">Sed Diam Nonummy Nibh &nbsp;Consectetuer &nbsp;Elit <b>+</b></div></div>

<!-- contact -->
<div class="contact-ghost">CONTACT</div>
<div class="footer"></div>
<div class="contact-card">
  <form class="contact-form">
    <h2 style="position:absolute;left:0;width:256px;text-align:center;top:48px;left:120px">Contact Us</h2>
    <div class="field" style="left:36px;top:90px;width:204px">Name</div>
    <div class="field" style="left:254px;top:90px;width:204px">Email</div>
    <div class="field" style="left:36px;top:139px;width:204px">Phone No</div>
    <div class="field" style="left:254px;top:139px;width:204px">Subject</div>
    <div class="field" style="left:36px;top:188px;width:422px;height:70px">Message</div>
    <div class="btn" style="left:167px;top:282px">Get Franchisee <span class="dot"><i></i></span></div>
  </form>
  <div class="contact-info">
    <h2 style="margin-bottom:22px">Contact Details</h2>
    <div class="info-row"><span class="ico"><svg width="12" height="14" viewBox="0 0 12 14"><path d="M6 13S1 8 1 5a5 5 0 0110 0c0 3-5 8-5 8z" fill="none" stroke="#f39a12" stroke-width="1.4"/><circle cx="6" cy="5" r="1.6" fill="#f39a12"/></svg></span>123, Lorem Ipsum dolor Lorem Ipsum<br>is dummy text.</div>
    <div class="info-row"><span class="ico"><svg width="12" height="12" viewBox="0 0 12 12"><path d="M2 1l2 0 1 3-1.5 1a7 7 0 003.5 3.5L8 7l3 1v2a1 1 0 01-1 1A9 9 0 011 2a1 1 0 011-1z" fill="#f39a12"/></svg></span>+ 123 456 7890</div>
    <div class="info-row"><span class="ico"><svg width="12" height="10" viewBox="0 0 12 10"><rect x="0.7" y="0.7" width="10.6" height="8.6" fill="none" stroke="#f39a12" stroke-width="1.2"/><path d="M1 1l5 4 5-4" fill="none" stroke="#f39a12" stroke-width="1.2"/></svg></span>info@petalcraftonline.com</div>
    <div class="social"><span><i></i>Friendbook</span><span><i></i>Chirper</span><span><i></i>WorkLink</span></div>
  </div>
</div>

<div class="abs brand" style="left:185px;top:4384px;font-size:24px"><span class="mark"></span>Lantern Petals</div>
<nav class="foot-nav"><span>Home</span><span>About Us</span><span>For Supermarkets</span><span>For Franchisees</span><span>Contact Us</span></nav>
<p class="copyright">Copyright 2019 Petalcraft Online. All Rights Reserved</p>

</body>
</html>
```